Local fast-growing company in the service sector

We are looking for a modern business card design, which should also appear on our letterheads

Target Market(s)

Private and industrial sectors

Contact Information for Business Card

Vorname Name
Kellberger Str. 18
74189 Lindenau
Tel.: 07146-839214-0
Name@agentur-kvtl.de

Colors
9d9d9d
919191
aaaaaa

Requirements
Must have
• The logo (file) in silver

```html
<!DOCTYPE html>
<html lang="de">
<head>
<meta charset="utf-8">
<title>KVTL Visitenkarte</title>
<link href="https://fonts.googleapis.com/css2?family=Arimo:wght@400;700&display=swap" rel="stylesheet">
<style>
  :root {
    --stage: #2b2b2b;
    --card-top: #ffffff;
    --card-bottom: #e9e9e9;
    --silver: #9d9d9d;
    --silver-mid: #919191;
    --silver-light: #aaaaaa;
    --band: #b4b4b4;
    --band-edge: #d2d2d2;
    --ink: #1e1e1e;
    --ink-soft: #3a3a3a;
  }
  * { box-sizing: border-box; margin: 0; padding: 0; }
  html, body { width: 1200px; height: 997px; overflow: hidden; }
  body {
    background: var(--stage);
    font-family: "Arimo", Arial, sans-serif;
    position: relative;
  }
  .business-card {
    position: absolute;
    left: 150px; top: 207px;
    width: 900px; height: 582px;
    background: linear-gradient(160deg, var(--card-top) 0%, var(--card-bottom) 100%);
    overflow: hidden;
  }
  .brand {
    position: absolute; left: 60px; top: 120px;
    display: flex; align-items: center; gap: 22px;
  }
  .brand-square {
    width: 96px; height: 96px;
    background: var(--silver-light);
  }
  .brand-text { display: flex; flex-direction: column; }
  .brand-name {
    font-size: 92px; font-weight: 700; line-height: 0.9;
    color: var(--silver-mid); letter-spacing: 2px;
  }
  .brand-web {
    font-size: 30px; font-weight: 400; color: var(--silver-mid);
    letter-spacing: 3px; margin-top: 4px;
  }
  .holder {
    position: absolute; right: 40px; top: 222px; text-align: right;
  }
  .holder-name {
    font-size: 26px; font-weight: 700; color: var(--silver-mid);
    text-transform: uppercase; letter-spacing: 0.5px;
  }
  .holder-role {
    font-size: 19px; font-weight: 700; color: var(--ink);
    text-transform: uppercase; margin-top: 2px;
  }
  .holder-tab {
    position: absolute; right: 0; top: 222px;
    width: 14px; height: 30px;
    background: var(--silver); border-radius: 6px 0 0 6px;
  }
  .contacts {
    position: absolute; left: 40px; top: 388px;
    list-style: none; display: flex; flex-direction: column; gap: 14px;
  }
  .contact-item {
    display: flex; align-items: center; gap: 16px;
    font-size: 22px; color: var(--ink-soft);
  }
  .contact-icon { width: 22px; height: 22px; flex: none; }
  .address-band {
    position: absolute; left: 0; right: 0; bottom: 44px; height: 66px;
    background: var(--band);
    border-top: 8px solid var(--band-edge);
    display: flex; align-items: center; justify-content: flex-end;
    padding-right: 90px;
  }
  .address {
    font-size: 24px; color: var(--ink-soft);
    text-transform: uppercase; letter-spacing: 2px; font-style: normal;
    white-space: nowrap;
  }
  .card-foot {
    position: absolute; left: 0; right: 0; bottom: 0; height: 44px;
    background: linear-gradient(180deg, #e2e2e2, #f2f2f2);
  }
</style>
</head>
<body>
  <article class="business-card">
    <div class="brand">
      <div class="brand-square"></div>
      <div class="brand-text">
        <span class="brand-name">KVTL</span>
        <span class="brand-web">agentur-kvtl.de</span>
      </div>
    </div>

    <div class="holder">
      <p class="holder-name">Jonas M. Keller</p>
      <p class="holder-role">President &amp; CEO</p>
    </div>
    <div class="holder-tab"></div>

    <ul class="contacts">
      <li class="contact-item">
        <svg class="contact-icon" viewBox="0 0 22 22" aria-hidden="true">
          <circle cx="11" cy="11" r="11" fill="var(--silver-light)"/>
          <path d="M6 8.5c0-1 .8-1.5 1.5-1.5h7c.7 0 1.5.5 1.5 1.5v1h-2.5v-1h-5v1H6z M7 11h8l1 4H6z" fill="#f4f4f4"/>
        </svg>
        <span>07146-839214-0</span>
      </li>
      <li class="contact-item">
        <svg class="contact-icon" viewBox="0 0 22 22" aria-hidden="true">
          <circle cx="11" cy="11" r="11" fill="var(--silver-light)"/>
          <rect x="5.5" y="7" width="11" height="8" fill="#f4f4f4"/>
          <path d="M5.5 7l5.5 4.5L16.5 7" fill="none" stroke="var(--silver-light)" stroke-width="1.2"/>
        </svg>
        <span>Name@agentur-kvtl.de</span>
      </li>
    </ul>

    <div class="address-band">
      <address class="address">Kellberger Str. 18, 74189 Lindenau</address>
    </div>
    <div class="card-foot"></div>
  </article>
</body>
</html>
```